Aquatic View

We need a web design for a new window cleaning company name Tidewell Glass Care. We are located in Grand Cayman, Cayman Islands. We are a small company, a team of husband and wife. Our services include residencial interior and exterior window cleaning and commercial. Extra services such as ceiling fans cleaning, mirrors, high dusting. Home cleaning services. Power washing. Explaining the service. We want a modern, beachy style with aquatic colors. We want to use our domain name "tidewellglasscare.ky". We want to portray a clean, modern and professional design.

Target Market(s)

Big Home owners

Industry/Entity Type

Cleaning Service

Contact Information for Business Card

Company Name: Tidewell Glass Care
Name: Desmond Farrowby owner/manager
Phone: 345-9170452
Email: desmond@tidewellglasscare.ky
Website: tidewellglasscare.ky
Address: P.O.Box 2486 GT, George Town, Grand Cayman KY1-1203 Cayman Islands

Number of Pages Required

2 page

Font styles to use
Sans Serif

Colors
0592cd
0455a3
33a6d7
85cae6
cadf82
abd036
fbf289

Requirements
Nice to have
• Pictures of an ocean view and palm trees from clear windows.
• https://quorvantel.com/bidlinker/
• Use the above for "free estimate".

```html
<!DOCTYPE html>
<html lang="en">
<head>
<meta charset="utf-8">
<title>Tidewell Glass Care</title>
<link href="https://fonts.googleapis.com/css2?family=Lato:ital,wght@0,400;0,700;0,900;1,400&display=swap" rel="stylesheet">
<style>
:root{
  --ink:#222;
  --dark:#2b2b2b;
  --footer:#242424;
  --blue:#0592cd;
  --deep:#0455a3;
  --red:#c0161c;
  --text:#666;
  --line:#d9d9d9;
  --white:#fff;
}
*{box-sizing:border-box;margin:0;padding:0}
html,body{width:1200px;height:1001px;overflow:hidden}
body{font-family:'Lato',sans-serif;background:var(--white);position:relative;color:var(--text)}
.topbar{position:absolute;left:0;top:0;width:1200px;height:36px;background:var(--dark)}
.topbar .phone{position:absolute;right:116px;top:5px;display:flex;align-items:center;gap:7px;color:var(--white);font-size:20px;font-weight:700}
.header{position:absolute;left:0;top:36px;width:1200px;height:67px;background:var(--white)}
.brand{position:absolute;left:122px;top:8px;width:140px;height:104px;border-radius:70px 70px 0 0;background:var(--white);display:flex;flex-direction:column;align-items:center;justify-content:center;gap:6px;z-index:3}
.brand .mark{width:34px;height:34px;border-radius:50%;background:var(--blue)}
.brand .name{font-size:14px;font-weight:900;color:var(--deep);text-align:center;line-height:1.1}
.nav{position:absolute;right:116px;top:62px;display:flex;align-items:center;font-size:13px;font-weight:700;color:var(--ink);z-index:3}
.nav a{color:inherit;text-decoration:none;padding:3px 12px;border-left:1px solid var(--line)}
.nav a:first-child{border:1px solid var(--blue);color:var(--blue);margin-right:8px}
.nav a:nth-child(2){border-left:none}
.nav a:nth-child(3){padding:3px 22px 3px 14px}
.nav a:nth-child(4){padding:3px 0 3px 20px}
.hero{position:absolute;left:0;top:103px;width:1200px;height:441px;background:linear-gradient(100deg,#b9a89a 0%,#d7c7b9 30%,#c9b7a5 55%,#86a060 80%,#5c8a3c 100%)}
.hero-title{position:absolute;right:118px;top:150px;text-align:right;color:var(--white);font-size:26px;font-weight:700;line-height:41px;text-shadow:0 1px 3px rgba(0,0,0,.35)}
.arrow{position:absolute;top:198px;width:35px;height:35px;border-radius:50%;background:rgba(255,255,255,.7);display:flex;align-items:center;justify-content:center}
.arrow.prev{left:34px}.arrow.next{right:34px}
.band{position:absolute;left:0;top:544px;width:1200px;height:200px;background:linear-gradient(#ddd,#fff)}
.card{position:absolute;left:99px;top:506px;width:1002px;height:349px;background:var(--white)}
.col{position:absolute;top:26px}
.col h2{font-size:17px;font-weight:900;color:var(--blue);letter-spacing:.3px;padding-bottom:9px;border-bottom:1px solid var(--line);position:relative;white-space:nowrap}
.col h2 span{color:var(--red)}
.col h2::after{content:"";position:absolute;left:0;bottom:-2px;width:86px;height:3px;background:var(--deep)}
.about{left:17px;width:265px}
.photo{margin-top:14px;width:265px;height:122px;border:1px solid #ccc;background:linear-gradient(120deg,#c9d6e2,#8aa7c4 55%,#3d6fa8)}
.about p{margin-top:10px;font-size:13px;line-height:20px;padding-left:2px}
.btn{display:inline-block;margin-top:9px;background:var(--deep);color:var(--white);font-size:13px;font-weight:700;padding:8px 9px}
.services{left:334px;width:334px}
.services p{font-size:12.7px;line-height:17px;padding-left:2px}
.services .intro{margin-top:12px}
.services h3{display:flex;align-items:center;gap:8px;font-size:15px;font-weight:700;color:var(--blue);margin-top:6px;margin-bottom:1px}
.divider{position:absolute;top:34px;width:1px;height:270px;background:#eee}
.inquiry{left:718px;width:266px}
.inquiry .pager{position:absolute;right:0;top:4px;font-size:13px;color:var(--ink)}
.field{margin-top:9px;height:30px;border:1px solid #ccc;font-size:12px;color:#555;padding:7px 6px}
.field.first{margin-top:17px}
.field.msg{height:72px}
.inquiry .btn{padding:8px 19px}
.footer{position:absolute;left:0;top:855px;width:1200px;height:107px;background:var(--footer);color:var(--white)}
.fnav{position:absolute;left:117px;top:20px;font-size:13px;font-weight:700;display:flex;gap:11px}
.finfo{position:absolute;left:116px;font-size:13px;display:flex;align-items:center;gap:7px}
.subscribe{position:absolute;right:116px;top:19px;display:flex;height:30px}
.subscribe .input{width:159px;background:var(--white);border-radius:3px 0 0 3px;font-size:11px;font-style:italic;color:#888;padding:8px 0 0 10px}
.subscribe .go{background:var(--deep);color:var(--white);font-size:12.5px;font-weight:700;padding:8px 9px}
.social{position:absolute;right:116px;top:68px;display:flex;gap:7px}
.social span{width:24px;height:24px;border:1.5px solid var(--white);border-radius:50%}
.copy{position:absolute;left:0;top:962px;width:1200px;height:39px;background:linear-gradient(var(--blue),var(--deep));color:var(--white);font-size:13px;text-align:center;padding-top:12px}
</style>
</head>
<body>
<div class="topbar">
  <div class="phone">
    <svg width="26" height="26" viewBox="0 0 26 26"><circle cx="13" cy="13" r="12" fill="none" stroke="#fff" stroke-width="1.5"/><path d="M9 7l3 3-1.5 2c1 2 2 3 4 4l2-1.5 3 3-2 2c-5 0-10-5-10-10z" fill="#fff"/></svg>
    012-345-6789
  </div>
</div>
<div class="header"></div>
<div class="brand"><span class="mark"></span><span class="name">Tidewell Glass Care</span></div>
<nav class="nav"><a>HOME</a><a>ABOUT US</a><a>SERIVCES</a><a>CONTACT US</a></nav>

<div class="hero" role="img" aria-label="Worker power washing a paved driveway beside a green lawn">
  <div class="hero-title">WE ARE<br>RESIDENTIAL,COMMERCIAL<br>CLEANING SERVICE FIRM</div>
  <div class="arrow prev"><svg width="12" height="14" viewBox="0 0 12 14"><path d="M9 1L3 7l6 6" fill="none" stroke="#555" stroke-width="3"/></svg></div>
  <div class="arrow next"><svg width="12" height="14" viewBox="0 0 12 14"><path d="M3 1l6 6-6 6" fill="none" stroke="#555" stroke-width="3"/></svg></div>
</div>
<div class="band"></div>

<main class="card">
  <section class="col about">
    <h2><span>ABOUT</span> TIDEWELL GLASS CARE</h2>
    <div class="photo" role="img" aria-label="Cleaner in blue uniform squeegeeing a large window"></div>
    <p>Lorem ipsum dolor sit amet, consectetuer adip iscing elit, sed diam nonummy nibh euismod magna aliquam erat volutpat.</p>
    <span class="btn">READ MORE</span>
  </section>
  <div class="divider" style="left:309px"></div>
  <section class="col services">
    <h2><span>OUR</span> SERVICES</h2>
    <p class="intro">Lorem ipsum dolor sit amet, consectetuer adip iscing elit sed diam nonummy nibh euismod magna.</p>
    <h3><svg width="22" height="18" viewBox="0 0 22 18"><path d="M11 1L1 9h3v8h14V9h3z" fill="#666"/></svg>Residential</h3>
    <p>Lorem ipsum dolor sit amet, consectetuer adip iscing elit sed diam nonummy nibh euismod magna.</p>
    <h3><svg width="22" height="18" viewBox="0 0 22 18"><path d="M2 17V6h5V1h8v5h5v11z" fill="#666"/><path d="M9 4h4M9 8h4M9 12h4M4 10h2M16 10h2" stroke="#fff" stroke-width="1.5"/></svg>Commercial</h3>
    <p>Lorem ipsum dolor sit amet, consectetuer adip iscing elit sed diam nonummy nibh euismod magna.</p>
    <h3 style="margin-top:10px"><svg width="22" height="20" viewBox="0 0 22 20"><circle cx="8" cy="8" r="5" fill="none" stroke="#666" stroke-width="3.5" stroke-dasharray="2.5 1.5"/><circle cx="16" cy="15" r="3" fill="none" stroke="#666" stroke-width="2.5" stroke-dasharray="2 1"/></svg>Extra Services</h3>
    <p>Lorem ipsum dolor sit amet, consectetuer adip iscing elit sed diam nonummy nibh euismod magna.</p>
  </section>
  <div class="divider" style="left:694px"></div>
  <section class="col inquiry">
    <h2><span>QUICK</span> INQUIRY</h2>
    <div class="pager">‹&nbsp;&nbsp;›</div>
    <div class="field first">Email</div>
    <div class="field">Phone</div>
    <div class="field">Email</div>
    <div class="field msg">Message</div>
    <span class="btn">SUBMIT</span>
  </section>
</main>

<footer class="footer">
  <div class="fnav"><span>Home</span><span>I</span><span>About Us</span><span>I</span><span>Serivces</span><span>&nbsp;&nbsp;I</span><span>Contact Us</span></div>
  <div class="finfo" style="top:52px"><svg width="12" height="16" viewBox="0 0 12 16"><path d="M6 1a5 5 0 0 1 5 5c0 4-5 9-5 9S1 10 1 6a5 5 0 0 1 5-5z" fill="#bbb"/><circle cx="6" cy="6" r="2" fill="#242424"/></svg>Lorem ipsum dolor sit amet consectetuer adimpisciged</div>
  <div class="finfo" style="top:76px"><svg width="17" height="17" viewBox="0 0 26 26"><circle cx="13" cy="13" r="12" fill="none" stroke="#bbb" stroke-width="2"/><path d="M9 7l3 3-1.5 2c1 2 2 3 4 4l2-1.5 3 3-2 2c-5 0-10-5-10-10z" fill="#bbb"/></svg>123-456-7890&nbsp;&nbsp;&nbsp;<svg width="11" height="8" viewBox="0 0 11 8"><rect width="11" height="8" fill="#bbb"/><path d="M0 0l5.5 4L11 0" fill="none" stroke="#242424"/></svg>info@tidewellglasscare.ky</div>
  <div class="subscribe"><div class="input">your e-mail address</div><div class="go">SUBSCRIBE</div></div>
  <div class="social"><span></span><span></span><span></span><span></span></div>
</footer>
<div class="copy">Copyright © 2015&nbsp; TidewellGlassCare. All Right Reserved</div>
</body>
</html>
```